UK landscaping company needs website

We, Brackwell Landscapes need a website design for a company based in Surrey, UK. The design should be bold and playful. We have three main areas of work driveways, paving and fencing. It shouldn't be too heavy in text and concentrate on the pictures from previous jobs we've completed. You may use stock images for the design, these can be changed if you are successful. Please don’t just copy the flyer it is just there to provide content.
We have a logo design which we would also like editing slightly.
Here are some of my local competitors
https://www.pelmarlandscapes.example.co.uk/

https://www.twinfirgardendesign.example.com/

https://kestbyrnlandscapes.example.co.uk/

Industry/Entity Type

Landscaping

Coding

Coded - Design and coding required

Number of Pages Required

3 page

Font styles to use
Sans Serif

Requirements
Must have
• Pictures of my previous jobs.
Must be mobile friendly
Easy to navigate
Nice to have
• Try to use different colours. It would be good to have some designs that aren’t just black and green.
I’d like some curves in the design.
Should not have
• We install hard landscaping. Think more building/construction and less plants and cutting grass.

```html
<!DOCTYPE html>
<html lang="en">
<head>
<meta charset="utf-8">
<title>Brackwell Landscapes</title>
<link rel="stylesheet" href="https://fonts.googleapis.com/css2?family=Rajdhani:wght@500;600;700&family=Raleway:ital,wght@0,400;0,500;1,400&display=swap">
<style>
:root{
  --green:#5cb531;
  --green-dark:#4a9a26;
  --black:#000;
  --ink:#222;
  --blush:#ede4e3;
  --grey:#6f6e70;
  --night:#2a2624;
  --muted:#8a8585;
  --white:#fff;
}
*{margin:0;padding:0;box-sizing:border-box}
html,body{width:1200px;height:4001px;overflow:hidden}
body{position:relative;font-family:"Raleway",sans-serif;color:var(--ink);background:var(--night)}
.abs{position:absolute}
.head{font-family:"Rajdhani",sans-serif;font-weight:700;letter-spacing:1px;white-space:nowrap}
.btn{position:absolute;display:flex;align-items:center;justify-content:center;border:2px solid var(--green);color:var(--green);font-family:"Rajdhani",sans-serif;font-weight:600;font-size:17px;letter-spacing:.5px;text-transform:uppercase}
.fill{position:absolute}

/* header */
.site-header{position:absolute;left:0;top:0;width:1200px;height:82px;background:var(--black)}
.brand{position:absolute;display:flex;align-items:center;gap:8px;font-family:"Rajdhani",sans-serif;font-weight:700;color:var(--white);white-space:nowrap}
.brand-dot{width:12px;height:12px;border-radius:50%;background:var(--green)}
.site-header .brand{left:112px;top:20px;font-size:32px}
.nav{position:absolute;left:388px;top:34px;display:flex;gap:22px;font-family:"Rajdhani",sans-serif;font-weight:600;font-size:13px;color:var(--white);text-transform:uppercase;white-space:nowrap}
.nav .active{color:var(--green)}

/* hero */
.hero{position:absolute;left:0;top:82px;width:1200px;height:593px}
.hero-photo{width:100%;height:100%;background:linear-gradient(135deg,#8a6f4e 0%,#b99465 30%,#4f7a2c 55%,#3d6522 75%,#a88a6a 100%)}
.hero-card{position:absolute;left:601px;top:110px;width:483px;height:344px;border:2px solid var(--green);background:rgba(0,0,0,.35)}
.hero-card .brand{right:-6px;top:-26px;font-size:30px;padding:0 8px}
.hero-title{position:absolute;left:34px;top:62px;font-size:38px;line-height:44px;color:var(--white)}
.hero-copy{position:absolute;left:36px;top:118px;width:430px;font-size:15px;line-height:29px;color:var(--white)}
.hero-start{left:40px;top:198px;width:157px;height:54px;border-color:var(--white);color:var(--white)}
.hero-call{position:absolute;left:236px;top:216px;font-size:12px;color:var(--white);display:flex;align-items:center;gap:6px;white-space:nowrap}
.hero-call b{font-family:"Rajdhani",sans-serif;font-weight:600;font-size:18px}
.hero-mail{position:absolute;left:0;width:100%;top:282px;text-align:center;font-size:15px;color:var(--white);display:flex;justify-content:center;align-items:center;gap:6px;white-space:nowrap}

/* about */
.about{position:absolute;left:0;top:675px;width:1200px;height:541px;background:var(--black)}
.about-title{left:113px;top:95px;font-size:48px;color:var(--green)}
.about-copy{position:absolute;left:113px;top:158px;width:492px;font-size:15.5px;line-height:34px;color:var(--white);text-align:justify}
.about-more{left:110px;top:384px;width:157px;height:54px}
.about-person{left:683px;top:16px;width:280px;height:525px;background:linear-gradient(180deg,#d8d3c8 0%,#7a7a7a 40%,#2f3d7a 80%,#303c72 100%);border-radius:120px 120px 0 0}

/* areas */
.areas{position:absolute;left:0;top:1216px;width:1200px;height:1270px;background:var(--blush)}
.areas-title{left:0;width:1200px;top:38px;text-align:center;font-size:48px;color:var(--green)}
.view-all{left:930px;top:45px;width:157px;height:54px}
.ring{position:absolute;z-index:5;width:358px;height:358px;border-radius:50%;border:5px solid var(--green)}
.service-title{position:absolute;font-family:"Rajdhani",sans-serif;font-weight:700;font-size:25px;color:var(--ink);letter-spacing:1px}
.service-copy{position:absolute;width:366px;font-size:15px;line-height:32px;color:var(--muted);text-align:justify}

/* reviews */
.reviews{position:absolute;left:0;top:2440px;width:1200px;height:470px;background:var(--green);clip-path:polygon(0 13px,100% 40px,100% 100%,0 96%)}
.reviews-title{left:0;width:1200px;top:140px;text-align:center;font-size:50px;color:var(--white)}
.quote{position:absolute;left:120px;width:960px;top:218px;text-align:center;font-style:italic;font-size:16px;line-height:35px;color:var(--white)}
.reviewer{position:absolute;left:0;width:1200px;top:338px;text-align:center;color:var(--white)}
.reviewer .name{font-style:italic;font-size:16px}
.reviewer .role{font-size:12px;margin-top:4px}
.reviewer .score{font-size:11px;margin-top:2px}
.stars{display:flex;justify-content:center;gap:10px;margin-top:10px}

/* gallery and footer */
.lower{position:absolute;left:0;top:2898px;width:1200px;height:1103px;background:linear-gradient(180deg,#2d2a27 0%,#3a3430 40%,#2e2a27 100%)}
.gallery-title{left:0;width:1200px;top:132px;text-align:center;font-size:50px;color:var(--green)}
.shot{position:absolute;top:214px;width:236px;height:272px}
.dots{position:absolute;left:532px;top:524px;display:flex;gap:16px}
.dots span{width:14px;height:14px;border-radius:50%;border:2px solid var(--green)}
.dots .on{background:var(--green)}
.news-title{left:110px;top:640px;font-size:36px;color:var(--white);font-weight:600}
.news-sub{position:absolute;left:113px;top:692px;font-size:15px;color:var(--white)}
.news-form{position:absolute;left:630px;top:651px;width:457px;height:50px;background:var(--white);border-radius:25px;overflow:hidden}
.news-form .field{position:absolute;left:26px;top:17px;font-size:13px;color:#777;display:flex;align-items:center;gap:8px}
.news-form .submit{position:absolute;right:0;top:0;width:173px;height:50px;background:var(--green);border-radius:25px;color:var(--white);font-family:"Rajdhani",sans-serif;font-weight:700;font-size:19px;display:flex;align-items:center;justify-content:center;letter-spacing:1px}
.rule{position:absolute;left:110px;width:977px;height:1px;background:#6b6561}
.foot-col{position:absolute;top:794px;color:var(--white)}
.foot-col h4{font-family:"Rajdhani",sans-serif;font-weight:700;font-size:19px;letter-spacing:1px;margin-bottom:12px}
.foot-col li{list-style:none;font-size:15.5px;line-height:34px}
.social{position:absolute;left:987px;top:814px;display:flex;gap:14px}
.social span{width:14px;height:14px;border-radius:50%;background:var(--white)}
.copy{position:absolute;left:0;width:1200px;top:1048px;text-align:center;font-size:15px;color:var(--white)}
</style>
</head>
<body>

<header class="site-header">
  <div class="brand">BRACKWELL<span class="brand-dot"></span></div>
  <nav class="nav">
    <span class="active">Home</span><span>Landscaping</span><span>Driveways &amp; Paving</span><span>Construction</span><span>Work Gallery</span><span>Customer Care</span><span>Contact Us</span>
  </nav>
</header>

<section class="hero">
  <div class="hero-photo" role="img" aria-label="Finished garden with timber decking, raised sleeper beds, lawn and sandstone paving"></div>
  <div class="hero-card">
    <div class="brand">BRACKWELL<span class="brand-dot"></span></div>
    <h1 class="hero-title head">BRACKWELL LANDSCAPES</h1>
    <p class="hero-copy">Nemo enim ipsam voluptatem quia voluptas sit aspernatur dolores eos qui ratione voluptatem</p>
    <div class="btn hero-start">Get Started</div>
    <div class="hero-call">
      <svg width="13" height="13" viewBox="0 0 24 24"><path fill="#fff" d="M6.6 10.8a15 15 0 0 0 6.6 6.6l2.2-2.2c.3-.3.7-.4 1-.2 1.1.4 2.3.6 3.6.6.6 0 1 .4 1 1V20c0 .6-.4 1-1 1A17 17 0 0 1 3 4c0-.6.4-1 1-1h3.5c.6 0 1 .4 1 1 0 1.3.2 2.5.6 3.6.1.3 0 .7-.2 1z"/></svg>
      CALL NOW - <b>7700 900 418</b>
    </div>
    <div class="hero-mail">
      <svg width="17" height="13" viewBox="0 0 24 18"><rect width="24" height="18" rx="2" fill="#fff"/><path d="M1 2l11 8 11-8" stroke="#555" stroke-width="2" fill="none"/></svg>
      EMAIL - info@brackwell-landscapes.example.com
    </div>
  </div>
</section>

<section class="about">
  <svg class="abs" style="left:0;top:0" width="1200" height="541" viewBox="0 0 1200 541">
    <polygon points="601,541 1071,0 1200,0 1200,132 846,541" fill="#5cb531"/>
    <polygon points="970,541 1200,280 1200,541" fill="#6f6e70"/>
  </svg>
  <h2 class="about-title head abs">ABOUT US</h2>
  <p class="about-copy">Nemo enim ipsam voluptatem quia voluptas sit aspernatur aut odit aut fugit, sed quia consequuntur magni dolores eos qui ratione voluptatem sequi nesciunt. Neque porro quisquam est, qui dolorem ipsum quia dolor sit amet, consectetur, adipisci velit, sed quia non numquam eius modi tempora incidunt ut labore et dolore magnam aliquam quaerat voluptatem.</p>
  <div class="btn about-more">Read More</div>
  <div class="fill about-person" role="img" aria-label="Builder in hard hat and work overalls with arms folded"></div>
</section>

<section class="areas">
  <svg class="abs" style="left:0;top:0" width="1200" height="1237" viewBox="0 0 1200 1237" role="img" aria-label="Stone patio and slate paving beside raised flower beds">
    <defs><linearGradient id="patio" x1="0" y1="0" x2="1" y2="1"><stop offset="0" stop-color="#4d5a3a"/><stop offset=".45" stop-color="#8a8a88"/><stop offset="1" stop-color="#2f3440"/></linearGradient></defs>
    <polygon points="0,0 908,0 0,798" fill="url(#patio)"/>
  </svg>
  <h2 class="areas-title head abs">AREAS OF WORK</h2>
  <div class="btn view-all">View All</div>

  <div class="ring" style="left:319px;top:176px;background:linear-gradient(160deg,#6a7a4a 0%,#7c7d80 30%,#5d5f63 100%)" role="img" aria-label="Grey block paved driveway with drainage channel"></div>
  <div class="service-title" style="left:716px;top:270px">DRIVEWAYS</div>
  <p class="service-copy" style="left:711px;top:305px">Nemo enim ipsam voluptatem quia voluptas sit aspernatur aut odit aut fugit, sed quia consequuntur magni dolores eos qui ratione voluptatem sequi nesciunt</p>
  <div class="btn" style="left:711px;top:447px;width:157px;height:54px">Read More</div>

  <div class="service-title" style="left:307px;top:612px">PAVING</div>
  <p class="service-copy" style="left:307px;top:647px">Nemo enim ipsam voluptatem quia voluptas sit aspernatur aut odit aut fugit, sed quia consequuntur magni dolores eos qui ratione voluptatem sequi nesciunt</p>
  <div class="btn" style="left:307px;top:790px;width:159px;height:54px">Read More</div>
  <div class="ring" style="left:731px;top:553px;background:linear-gradient(200deg,#5a5652 0%,#4a4a4c 45%,#c9c6c0 100%)" role="img" aria-label="Curved paved path with gravel border beside a house"></div>

  <div class="ring" style="left:147px;top:957px;background:radial-gradient(circle,#b49a86 0%,#a78d7a 50%,#8f7d72 100%)" role="img" aria-label="Circular sandstone paving feature"></div>
  <div class="service-title" style="left:539px;top:990px">FENCING</div>
  <p class="service-copy" style="left:539px;top:1025px">Nemo enim ipsam voluptatem quia voluptas sit aspernatur aut odit aut fugit, sed quia consequuntur magni dolores eos qui ratione voluptatem sequi nesciunt</p>
  <div class="btn" style="left:539px;top:1167px;width:157px;height:54px">Read More</div>
</section>

<section class="lower">
  <h2 class="gallery-title head abs">WORK GALLERY</h2>
  <div class="shot" style="left:109px;background:linear-gradient(180deg,#7b6a5a,#cfcac4 60%,#5d8a3a)" role="img" aria-label="Timber pergola over pale paving"></div>
  <div class="shot" style="left:357px;background:linear-gradient(170deg,#6a5a4c,#4f8a2e 55%,#a8612e)" role="img" aria-label="Lawn with timber sleeper steps"></div>
  <div class="shot" style="left:605px;background:linear-gradient(180deg,#c9c2bb,#8f7a64 50%,#6a6a6a)" role="img" aria-label="Timber pergola and fenced patio"></div>
  <div class="shot" style="left:854px;background:linear-gradient(180deg,#7e9a5e,#8a6c48 45%,#4f8a2e)" role="img" aria-label="New timber fence panels along a lawn"></div>
  <div class="dots"><span></span><span></span><span class="on"></span><span></span><span></span></div>

  <h2 class="news-title head abs">SUBSCRIBE TO NEWSLETTER</h2>
  <p class="news-sub">Lorem ipsum dolor sit amet, consectetur adipiscing</p>
  <div class="news-form">
    <div class="field"><svg width="14" height="11" viewBox="0 0 24 18"><rect width="24" height="18" rx="2" fill="#777"/><path d="M1 2l11 8 11-8" stroke="#fff" stroke-width="2" fill="none"/></svg>Enter email address</div>
    <div class="submit">SUBMIT</div>
  </div>
  <div class="rule" style="top:745px"></div>

  <div class="foot-col" style="left:110px"><h4>SERVICES</h4><ul><li>Driveways</li><li>Paving</li><li>Fencing</li></ul></div>
  <div class="foot-col" style="left:287px"><h4>ABOUT</h4><ul><li>About Us</li><li>Team</li><li>Terms &amp; conditions</li><li>Privacy Policy</li><li>Review</li></ul></div>
  <div class="foot-col" style="left:515px"><h4>QUICK LINKS</h4><ul><li>Home</li><li>About</li><li>Services</li><li>Blogs</li><li>Conatact</li></ul></div>
  <div class="foot-col" style="left:723px"><h4>HELP</h4><ul><li>Information</li><li>Support</li></ul></div>
  <div class="social"><span></span><span></span><span></span><span></span></div>

  <div class="rule" style="top:1019px"></div>
  <p class="copy">© 2020 All Rights Reserved</p>
</section>

<section class="reviews">
  <h2 class="reviews-title head abs">CLIENT REVIEWS</h2>
  <svg class="abs" style="left:96px;top:250px" width="14" height="24" viewBox="0 0 14 24"><path d="M12 2L3 12l9 10" stroke="#fff" stroke-width="2" fill="none"/></svg>
  <svg class="abs" style="left:1092px;top:250px" width="14" height="24" viewBox="0 0 14 24"><path d="M2 2l9 10-9 10" stroke="#fff" stroke-width="2" fill="none"/></svg>
  <p class="quote">“ Nemo enim ipsam voluptatem quia voluptas sit aspernatur aut odit aut fugit, sed quia consequuntur magni dolores eos qui ratione voluptatem sequi nesciunt. Neque porro quisquam est, qui dolorem ipsum quia dolor sit amet, consectetur, adipisci velit, sed quia non numquam eius modi tempora incidunt ut labore et dolore magnam aliquam quaerat voluptatem. ”</p>
  <div class="reviewer">
    <div class="name">Daniel Hartley</div>
    <div class="role">Lorem ipsum</div>
    <div class="stars">
      <svg width="17" height="17" viewBox="0 0 24 24"><path fill="#fff" d="M12 1l3.4 7 7.6 1-5.5 5.3 1.3 7.7L12 18.3 5.2 22l1.3-7.7L1 9l7.6-1z"/></svg>
      <svg width="17" height="17" viewBox="0 0 24 24"><path fill="#fff" d="M12 1l3.4 7 7.6 1-5.5 5.3 1.3 7.7L12 18.3 5.2 22l1.3-7.7L1 9l7.6-1z"/></svg>
      <svg width="17" height="17" viewBox="0 0 24 24"><path fill="#fff" d="M12 1l3.4 7 7.6 1-5.5 5.3 1.3 7.7L12 18.3 5.2 22l1.3-7.7L1 9l7.6-1z"/></svg>
      <svg width="17" height="17" viewBox="0 0 24 24"><path fill="#fff" d="M12 1l3.4 7 7.6 1-5.5 5.3 1.3 7.7L12 18.3 5.2 22l1.3-7.7L1 9l7.6-1z"/></svg>
      <svg width="17" height="17" viewBox="0 0 24 24"><path fill="#fff" d="M12 1l3.4 7 7.6 1-5.5 5.3 1.3 7.7L12 18.3 5.2 22l1.3-7.7L1 9l7.6-1z"/></svg>
    </div>
    <div class="score">5/5</div>
  </div>
</section>

</body>
</html>
```